New Bicycle shop business card

Hi!
I'm looking for a business card for my new proffesional bike mechanics shop. This shop is only for fixing broken bikes and not selling bikes.
Peferbly a modern and sleek and modern design.
Colors: black, grey, red, white
Information:
Name: Rijwielwerkplaats Vanhoutte
Shop owner: Bart Vanhoutte & Marieke Segers
Website: www.rijwielwerkplaats-vanhoutte.be
Email: info@rijwielwerkplaats-vanhoutte.be
Phone number: +32471902368
Street adres: Kerkweg 46
9940 Bellebeke
Slogan/shop information: Herstellingen van alle merken.
Logo: see files.
Target Market(s)
People who seek a mechanic to fix or upgrade their bikes.
Contact Information for Business Card
Information:
Website: info@rijwielwerkplaats-vanhoutte.be
9940 Bellebeke
Logo: see files.

```html
<!DOCTYPE html>
<html lang="nl">
<head>
<meta charset="utf-8">
<title>Rijwielwerkplaats Vanhoutte – visitekaartje</title>
<link href="https://fonts.googleapis.com/css2?family=Lato:wght@400;700&display=swap" rel="stylesheet">
<style>
  :root {
    --backdrop: #3a3a3a;
    --brand-red: #e0143c;
    --ink: #1d1716;
    --paper: #ffffff;
  }
  * { margin: 0; padding: 0; box-sizing: border-box; }
  html, body { width: 1200px; height: 900px; overflow: hidden; }
  body {
    position: relative;
    background: var(--backdrop);
    font-family: "Lato", Arial, sans-serif;
    color: var(--ink);
  }
  .card {
    position: absolute;
    top: 200px;
    width: 310px;
    height: 502px;
    box-shadow: 2px 4px 6px rgba(0,0,0,0.55);
  }
  .card--front {
    left: 253px;
    background: var(--paper);
    border-radius: 62px 0 62px 0;
  }
  .card--back {
    left: 627px;
    background: var(--brand-red);
    border-radius: 0 62px 0 62px;
  }

  /* front: brand block */
  .brand {
    position: absolute;
    top: 98px;
    left: 0;
    width: 100%;
    text-align: center;
  }
  .brand__mark {
    display: block;
    width: 58px;
    height: 58px;
    margin: 0 auto 24px;
    background: var(--brand-red);
  }
  .brand__name {
    font-weight: 700;
    font-size: 19px;
    letter-spacing: 1.5px;
    line-height: 1.25;
    text-transform: uppercase;
    color: var(--ink);
  }

  /* front: contact block */
  .contact {
    position: absolute;
    left: 33px;
    top: 314px;
    font-size: 14px;
    line-height: 18px;
  }
  .contact__names {
    color: var(--brand-red);
    text-transform: uppercase;
    font-size: 13.5px;
  }
  .contact__role { margin-bottom: 7px; }
  .contact__list { list-style: none; font-size: 13.2px; }
  .contact__item { display: flex; align-items: center; gap: 5px; }
  .contact__icon { width: 11px; height: 11px; flex: none; fill: var(--brand-red); }
  .contact__address { margin-top: 9px; font-style: normal; }

  /* back */
  .back-brand {
    position: absolute;
    top: 170px;
    left: 0;
    width: 100%;
    text-align: center;
    color: var(--paper);
  }
  .back-brand__mark {
    display: block;
    width: 70px;
    height: 70px;
    margin: 0 auto 22px;
    border-radius: 50%;
    background: var(--paper);
  }
  .back-brand__name {
    font-weight: 700;
    font-size: 18px;
    letter-spacing: 1.5px;
    line-height: 1.3;
    text-transform: uppercase;
  }
  .tagline {
    position: absolute;
    top: 437px;
    left: 0;
    width: 100%;
    text-align: center;
    color: var(--paper);
    font-size: 14.5px;
    text-transform: uppercase;
  }
</style>
</head>
<body>

<section class="card card--front">
  <div class="brand">
    <span class="brand__mark"></span>
    <p class="brand__name">Rijwielwerkplaats<br>Vanhoutte</p>
  </div>

  <div class="contact">
    <p class="contact__names">Bart Vanhoutte &amp; Marieke Segers</p>
    <p class="contact__role">Owner</p>
    <ul class="contact__list">
      <li class="contact__item">
        <svg class="contact__icon" viewBox="0 0 12 12" aria-hidden="true"><path d="M1 4c0-2 2-3 5-3s5 1 5 3l-2 1-1-2H4L3 5 1 4zM3 6h6l1.5 5h-9z"/></svg>
        +32471902368
      </li>
      <li class="contact__item">
        <svg class="contact__icon" viewBox="0 0 12 12" aria-hidden="true"><path d="M0 2h12v8H0z"/><path d="M0 2l6 5 6-5" fill="none" stroke="#fff" stroke-width="1.2"/></svg>
        info@rijwielwerkplaats-vanhoutte.be
      </li>
      <li class="contact__item">
        <svg class="contact__icon" viewBox="0 0 12 12" aria-hidden="true"><circle cx="6" cy="6" r="5.5"/><path d="M3 3.5l2 1-1 2 2 1v2M8 2.5l-1 2 2 1" fill="none" stroke="#fff" stroke-width="1"/></svg>
        www.rijwielwerkplaats-vanhoutte.be
      </li>
    </ul>
    <address class="contact__address">Kerkweg 46<br>9940 Bellebeke</address>
  </div>
</section>

<section class="card card--back">
  <div class="back-brand">
    <span class="back-brand__mark"></span>
    <p class="back-brand__name">Rijwielwerkplaats<br>Vanhoutte</p>
  </div>
  <p class="tagline">Herstellingen van alle merken</p>
</section>

</body>
</html>
```